Website Redesign - We Need Your Magic!

Hello we are looking for you to help us re-design a high end and professional website for a high-end private school.

Here is the current site: http://www.ferndalecrest.com/

NOTE THIS IS DESIGN ONLY, NO CODING :)

The image they want to portray is that of high quality sports and education, in a creative "un-stiff" way.

Menu Bar: Horizontal

Look and Feel:

Site Colors: Dark green and a Gold yellow (logos are attached)

This site will represent a school so the look must be clean, bold, and classy. The site must have a very clean user interface, with things easily recognizable. Think simple.

The site should be visually appealing! If you come to me with templates, or a ton of text you will be out.

This site should be outside the box, we do not want boring, we do not want status quo. This site should instill excitement, innovation, and athletics.

So the main points again are:

1. High-end and classy look, with creative feel
2. Simple and clear navigation style
3. To cover the Junior and High School - Ferndale Crest College Schools

Think outside the box. We look forward to seeing what you come up with!!

Thank you for helping us create an amazing site for the school!

Industry/Entity Type

School

```html
<!DOCTYPE html>
<html lang="en">
<head>
<meta charset="utf-8">
<title>Ferndale Crest College</title>
<link href="https://fonts.googleapis.com/css2?family=Oswald:wght@400;500;600&family=Open+Sans:wght@400;600;700&display=swap" rel="stylesheet">
<style>
:root{
  --green:#0b5522;
  --green-dark:#074219;
  --green-deep:#05330f;
  --green-row:#0e5e28;
  --green-row-alt:#0a4f20;
  --green-line:#1d6d35;
  --gold:#f4e01c;
  --white:#ffffff;
  --text:#e6efe8;
  --head:'Oswald',sans-serif;
  --body:'Open Sans',sans-serif;
}
*{box-sizing:border-box;margin:0;padding:0}
html,body{width:1200px;height:2769px;overflow:hidden}
body{background:var(--green);color:var(--text);font-family:var(--body);font-size:12px;line-height:1.6;position:relative}
.abs{position:absolute}
.h{font-family:var(--head);font-weight:500;font-size:20px;color:var(--white);text-transform:uppercase;letter-spacing:.3px;line-height:1}
.h em{font-style:normal;color:var(--gold)}
.h::after{content:"";display:block;width:42px;height:3px;background:var(--gold);margin-top:8px}

/* header */
.brand{left:162px;top:14px;width:110px;height:100px;display:flex;flex-direction:column;align-items:center;justify-content:center;gap:6px}
.brand-mark{width:54px;height:54px;background:var(--gold);border-radius:4px}
.brand-name{font-family:var(--head);font-size:11px;color:var(--gold);text-align:center;line-height:1.1;text-transform:uppercase}
.info{left:653px;top:22px;display:flex;gap:8px;align-items:center}
.info small{display:block;font-size:10px;color:var(--white);letter-spacing:.5px;text-transform:uppercase}
.info strong{font-family:var(--head);font-size:22px;color:var(--gold);font-weight:500;line-height:1.1}
.search{left:865px;top:24px;width:173px}
.search small{display:block;font-size:10px;color:var(--white);text-transform:uppercase;margin-bottom:4px}
.search-box{height:22px;background:var(--white);font-size:9px;color:#777;padding:3px 6px;position:relative}
.search-box svg{position:absolute;right:6px;top:5px}
.nav{right:162px;top:94px;display:flex;gap:22px;font-family:var(--head);font-size:13px;color:var(--white);text-transform:uppercase}
.nav .on{border-bottom:2px solid var(--gold);padding-bottom:3px}

/* hero */
.hero{left:0;top:138px;width:1200px;height:480px;display:grid;grid-template-columns:242px 243px 235px 238px 242px;grid-template-rows:1fr 1fr;gap:2px}
.tile{display:block}

/* welcome */
.welcome{left:162px;top:660px;width:500px}
.welcome p{margin-top:16px}
.video{left:685px;top:667px;width:353px;height:240px;border:3px solid var(--green-line);background:linear-gradient(180deg,#8fa7a9,#b7a785 55%,#5e6e3a)}
.play{position:absolute;left:50%;top:50%;width:54px;height:54px;margin:-27px 0 0 -27px}
.rule{left:162px;top:950px;width:876px;height:1px;background:var(--green-line)}

/* notes */
.note{top:990px;width:400px}
.note-body{display:flex;gap:16px;margin-top:24px}
.note-photo{flex:0 0 146px;height:146px;border:3px solid var(--green-line)}
.note-body p{font-size:11.5px;line-height:1.65}
.more{display:inline-block;margin-top:10px;background:var(--green-deep);border:1px solid var(--green-line);color:var(--gold);font-size:10px;padding:3px 9px}

/* calendar */
.cal{left:162px;top:1345px;width:876px}
.cal-head,.cal-row{display:grid;grid-template-columns:228px 216px 216px 216px}
.cal-head{margin-top:26px;font-family:var(--head);font-size:14px;color:var(--gold);text-transform:uppercase;text-align:center;height:38px}
.cal-row{height:54px;align-items:center;font-size:10.5px;text-align:center;line-height:1.45;color:var(--white)}
.cal-row:nth-child(odd){background:var(--green-row)}
.cal-row:nth-child(even){background:var(--green-row-alt)}
.cal-row b{font-family:var(--head);font-weight:500;font-size:14px;text-transform:uppercase;text-align:left;padding-left:14px}
.btn{top:1793px;width:276px;height:46px;background:var(--gold);color:var(--green-deep);font-family:var(--head);font-size:13px;text-transform:uppercase;display:flex;align-items:center;justify-content:center}

/* events */
.events{left:162px;top:1912px}
.event{top:1972px;width:200px}
.event-img{height:130px;border:3px solid var(--green-line)}
.event-date{font-family:var(--head);font-size:14px;color:var(--white);margin-top:14px;text-transform:uppercase}
.event-title{font-size:10.5px}
.sports{left:835px;top:1912px;width:203px}
.sports ul{list-style:none;margin-top:28px;font-size:11.5px;color:var(--white)}
.sports li{height:39px}

/* partners */
.partner{top:2257px;width:150px;height:88px;background:var(--white);display:flex;align-items:center;justify-content:center}
.partner span{width:96px;height:40px;background:#d9d9d9;border-radius:4px}

/* footer */
.footer{left:0;top:2432px;width:1200px;height:280px;background:var(--green-dark)}
.touch{left:162px;top:2462px}
.contact{width:260px;display:flex;gap:12px}
.contact .ic{flex:0 0 28px;height:28px;border:1.5px solid var(--gold);border-radius:50%;display:flex;align-items:center;justify-content:center}
.contact b{display:block;font-size:10.5px;color:var(--gold);text-transform:uppercase}
.contact p{font-size:10.5px;line-height:1.5;color:var(--white)}
.signup{left:762px;top:2405px;width:276px;height:283px;background:var(--green-line);padding:22px 22px}
.signup p{font-size:10.5px;margin-top:18px;color:var(--white);line-height:1.55}
.field{height:28px;background:var(--white);font-size:9.5px;color:#777;padding:6px 8px;margin-top:10px}
.actions{display:flex;gap:10px;margin-top:14px}
.actions span{height:28px;padding:0 14px;display:flex;align-items:center;font-family:var(--head);font-size:12px;text-transform:uppercase}
.sub{background:var(--gold);color:var(--green-deep)}
.unsub{background:var(--green-deep);color:var(--white)}
.bar{left:0;top:2712px;width:1200px;height:57px;background:var(--green-deep)}
.copy{left:162px;top:2732px;font-size:10.5px;color:var(--white)}
.social{left:898px;top:2727px;display:flex;gap:8px}
.social span{width:18px;height:18px;border-radius:50%;background:var(--green-line)}
.social .share{width:40px;border-radius:3px}
</style>
</head>
<body>

<header>
  <div class="abs brand"><span class="brand-mark"></span><span class="brand-name">Ferndale Crest</span></div>
  <div class="abs info">
    <svg width="18" height="24" viewBox="0 0 18 24"><rect x="2" y="1" width="14" height="22" rx="2" fill="#fff"/><rect x="4" y="4" width="10" height="12" fill="#0b5522"/></svg>
    <div><small>Information Call</small><strong>0771 384 290</strong></div>
  </div>
  <div class="abs search"><small>Search Now!</small>
    <div class="search-box">Enter Your Keyword...
      <svg width="11" height="11" viewBox="0 0 11 11"><circle cx="4.5" cy="4.5" r="3.5" fill="none" stroke="#777" stroke-width="1.4"/><line x1="7" y1="7" x2="10" y2="10" stroke="#777" stroke-width="1.4"/></svg>
    </div>
  </div>
  <nav class="abs nav"><span class="on">Home</span><span>About</span><span>Academics</span><span>Sports</span><span>Joining Ferndale Crest</span><span>Working at the College</span><span>Contact</span></nav>
</header>

<section class="abs hero">
  <span class="tile" role="img" aria-label="Rider jumping a horse over a fence" style="background:linear-gradient(160deg,#6f8a4c,#3f5a2a)"></span>
  <span class="tile" role="img" aria-label="Girls playing netball on a court" style="background:linear-gradient(160deg,#9a6a4c,#5b4a35)"></span>
  <span class="tile" role="img" aria-label="Hockey match on a grass field" style="background:linear-gradient(160deg,#8aa066,#52703a)"></span>
  <span class="tile" role="img" aria-label="Runners crossing a finish line" style="background:linear-gradient(160deg,#7d7057,#3f4a2c)"></span>
  <span class="tile" role="img" aria-label="Student in a dormitory room" style="background:linear-gradient(160deg,#b8b1a3,#6b5a48)"></span>
  <span class="tile" role="img" aria-label="Tree-lined school grounds" style="background:linear-gradient(160deg,#5e7a3d,#2f4a22)"></span>
  <span class="tile" role="img" aria-label="Students seated at an outdoor stone table" style="background:linear-gradient(160deg,#8b8f6e,#3d5a30)"></span>
  <span class="tile" role="img" aria-label="Group of students cheering" style="background:linear-gradient(160deg,#6b6652,#2e3a28)"></span>
  <span class="tile" role="img" aria-label="Sports field with goal posts" style="background:linear-gradient(160deg,#9bb07a,#4f7a33)"></span>
  <span class="tile" role="img" aria-label="Student working in a science lab" style="background:linear-gradient(160deg,#c9c6bd,#7a7467)"></span>
</section>

<section class="abs welcome">
  <h2 class="h">Welcome to <em>Ferndale Crest College</em></h2>
  <p>Welcome to Ferndale Crest Group of Schools where our School Motto is 'Sabatana' meaning Togetherness. We aim to work together in every aspect of School life, from academics to sport. Ferndale Crest College opened on 14th February 1983 and occupies 120 ha of land amidst the low hills of the Kestrel Range, 8km west of Marlow. This location encourages focus on School life away from the distractions and hustle and bustle of the larger towns.</p>
  <p>The day scholars have the option of selected bus drop off points for parents to collect day scholars closer to home. Ferndale Crest College offers a wide range of academic subjects alongside a varied sport and extra-curricular program.</p>
</section>
<div class="abs video" role="img" aria-label="Video still of the school main building">
  <svg class="play" viewBox="0 0 54 54"><circle cx="27" cy="27" r="25" fill="none" stroke="#fff" stroke-width="3"/><path d="M21 16 L39 27 L21 38Z" fill="#fff"/></svg>
</div>
<div class="abs rule"></div>

<section class="abs note" style="left:162px">
  <h2 class="h">Headmaster's <em>Welcome Note</em></h2>
  <div class="note-body">
    <span class="note-photo" role="img" aria-label="Portrait of the headmaster" style="background:linear-gradient(160deg,#6d8a5a,#2f5a2a)"></span>
    <div><p>Welcome to Ferndale Crest College. Here at the College we aim to encourage each pupil to be a self-confident, well-rounded individual. We aim to propel them to the highest level of achievement in both academics and extra-curricular activities to provide them with the life skills they will need when they leave the College and to prepare them to be of value to society.</p>
    <span class="more">Read More</span></div>
  </div>
</section>
<section class="abs note" style="left:626px;width:412px">
  <h2 class="h">Memorial Garden <em>Opened Speech Day 2011</em></h2>
  <div class="note-body">
    <span class="note-photo" role="img" aria-label="Students beside the memorial garden plaque" style="background:linear-gradient(160deg,#7a7a5e,#3a4e2c)"></span>
    <div><p>Every year the Lower Sixes choose a fundraising project - something for the community like a local orphanage or a local retirement home and then also something to uplift the school. To uplift the school, the Lower Six Class of 2010 decided that they would like to honour and remember people who played a part in the development of the school.</p>
    <span class="more">Read More</span></div>
  </div>
</section>

<section class="abs cal">
  <h2 class="h">School <em>Calender</em></h2>
  <div class="cal-head"><span></span><span>First Term</span><span>Second Term</span><span>Third Term</span></div>
  <div class="cal-body">
    <div class="cal-row"><b>Begins</b><span>Tuesday 14th January</span><span>Tuesday 13th May</span><span>Tuesday 9th September</span></div>
    <div class="cal-row"><b>1st Fixture Free</b><span>Friday 31st January –<br>Monday 3rd February</span><span>Friday 30th May –<br>Monday 2nd June</span><span>Friday 26th September –<br>Monday 29th September</span></div>
    <div class="cal-row"><b>Half-Term</b><span>Thursday 20th February –<br>Tuesday 25th February</span><span>Thursday 26th June –<br>Tuesday 1st July</span><span>Friday 10th October –<br>Tuesday 21st October</span></div>
    <div class="cal-row"><b>2nd Fixture Free</b><span>Friday 14th March –<br>Monday 17th March</span><span>Friday 18th July –<br>Monday 21st July</span><span>Friday 7th November –<br>Monday 10th November</span></div>
    <div class="cal-row"><b>Term Ends</b><span>Thursday 10th April</span><span>Friday 7th August</span><span>Thursday 4th December</span></div>
  </div>
</section>
<span class="abs btn" style="left:312px">Download Registration Form</span>
<span class="abs btn" style="left:612px">2nd Term 2014 Termly Calendar</span>

<h2 class="abs h events">Upcoming <em>Events</em></h2>
<article class="abs event" style="left:162px">
  <div class="event-img" role="img" aria-label="Girls basketball game" style="background:linear-gradient(160deg,#a07a5e,#5a5a3a)"></div>
  <div class="event-date">Fri 25 July 2014</div><div class="event-title">Basketball CSSA Top Schools</div>
</article>
<article class="abs event" style="left:388px">
  <div class="event-img" role="img" aria-label="Outdoor hockey practice" style="background:linear-gradient(160deg,#8da06a,#4e6e38)"></div>
  <div class="event-date">Sat 02 Aug 2013</div><div class="event-title">School Play - Public Performance</div>
</article>
<article class="abs event" style="left:612px">
  <div class="event-img" role="img" aria-label="Students gathered outdoors" style="background:linear-gradient(160deg,#7c7a5c,#3d4e2e)"></div>
  <div class="event-date">Thurs 07 Aug 2013</div><div class="event-title">Consultation for 4A, 5B, L6, U6</div>
</article>
<section class="abs sports">
  <h2 class="h">Sports <em>Announcements</em></h2>
  <ul><li>- Rugby</li><li>- Hockey Boys</li><li>- Soccer</li><li>- Hockey Girls</li><li>- Basketball Girls</li></ul>
</section>

<div class="abs partner" style="left:189px"><span></span></div>
<div class="abs partner" style="left:411px"><span></span></div>
<div class="abs partner" style="left:637px"><span></span></div>
<div class="abs partner" style="left:863px"><span></span></div>

<footer>
  <div class="abs footer"></div>
  <h2 class="abs h touch">Get in <em>Touch</em></h2>
  <div class="abs contact" style="left:162px;top:2528px">
    <span class="ic"><svg width="12" height="15" viewBox="0 0 12 15"><path d="M6 1a4.5 4.5 0 0 0-4.5 4.5C1.5 9 6 14 6 14s4.5-5 4.5-8.5A4.5 4.5 0 0 0 6 1z" fill="none" stroke="#f4e01c" stroke-width="1.4"/><circle cx="6" cy="5.5" r="1.5" fill="#f4e01c"/></svg></span>
    <div><b>Ferndale Crest College</b><p>Private Bag 12, Kestrel Road<br>Marlow 256894</p></div>
  </div>
  <div class="abs contact" style="left:473px;top:2528px">
    <span class="ic"><svg width="14" height="12" viewBox="0 0 14 12"><path d="M1 2l4-1 4 1 4-1v9l-4 1-4-1-4 1z" fill="none" stroke="#f4e01c" stroke-width="1.3"/></svg></span>
    <div><b>Map</b><p>Click here to see directions</p></div>
  </div>
  <div class="abs contact" style="left:162px;top:2650px">
    <span class="ic"><svg width="12" height="12" viewBox="0 0 12 12"><path d="M2 1h3l1 3-1.5 1a7 7 0 0 0 2.5 2.5L8 6l3 1v3a1 1 0 0 1-1 1A9 9 0 0 1 1 2a1 1 0 0 1 1-1z" fill="#f4e01c"/></svg></span>
    <div><b>Phone Number</b><p>0771 506 114 / 0771 384 290</p></div>
  </div>
  <div class="abs contact" style="left:473px;top:2650px">
    <span class="ic"><svg width="13" height="10" viewBox="0 0 13 10"><rect x="1" y="1" width="11" height="8" fill="none" stroke="#f4e01c" stroke-width="1.3"/><path d="M1 1l5.5 4.5L12 1" fill="none" stroke="#f4e01c" stroke-width="1.3"/></svg></span>
    <div><b>Email Us</b><p>office@ferndalecrest.com</p></div>
  </div>
  <section class="abs signup">
    <h2 class="h">Signup <em>Newsletter</em></h2>
    <p>If you would like to be added to the list of parents that receive the School Newsletter, please enter your details below.</p>
    <div class="field">Enter Your Name</div>
    <div class="field">Enter Your Email</div>
    <div class="actions"><span class="sub">Subscribe</span><span class="unsub">Unsubscribe</span></div>
  </section>
  <div class="abs bar"></div>
  <p class="abs copy">2014 Ferndale Crest College. All Rights Reserved.</p>
  <div class="abs social"><span class="share"></span><span></span><span></span><span></span></div>
</footer>

</body>
</html>
```